Specialised investor in e-mobility and energy wants business card design

We need a business card design that fits our existing corporate design. <The look and feel must be 'sharp'/'clean', dynamic, communicate momentum, professionalism etc (as one would imagine from a firm in the financial sector). We like the idea of a reverse-side of the card that includes the logo, and the name and contact details on the other. We expect the deliverable to be whatever format might be required to be able to get cards printed directly by a service such as kelmo press. Our website is www.zub.capital

```html
<!DOCTYPE html>
<html lang="en">
<head>
<meta charset="utf-8">
<title>ZUB Capital – Business Card</title>
<link rel="stylesheet" href="https://fonts.googleapis.com/css2?family=Montserrat:wght@400;500;700&display=swap">
<style>
  :root {
    --forest: #344f24;
    --forest-deep: #2b421d;
    --forest-soft: #3d5a2b;
    --leaf: #7ab648;
    --paper: #ffffff;
    --backdrop: #dcdcd9;
  }
  * { box-sizing: border-box; margin: 0; padding: 0; }
  html, body { width: 1200px; height: 801px; overflow: hidden; }
  body {
    background: var(--backdrop);
    font-family: "Montserrat", sans-serif;
    display: flex;
    align-items: center;
    justify-content: center;
    gap: 40px;
  }
  .card {
    width: 520px;
    height: 300px;
    position: relative;
    overflow: hidden;
    box-shadow: 0 10px 24px rgba(0,0,0,0.18);
  }

  /* Front side */
  .card-front { display: flex; background: var(--forest); }
  .brand-panel {
    width: 150px;
    background: var(--paper);
    display: flex;
    align-items: center;
    justify-content: center;
  }
  .brand-name {
    color: var(--forest);
    font-weight: 500;
    font-size: 22px;
    letter-spacing: 0.5px;
  }
  .details {
    position: relative;
    flex: 1;
    padding: 44px 0 0 40px;
    color: var(--paper);
  }
  .sweep { position: absolute; inset: 0; width: 100%; height: 100%; pointer-events: none; }
  .person-name {
    color: var(--leaf);
    font-weight: 700;
    font-size: 24px;
    letter-spacing: 1px;
    line-height: 1;
  }
  .person-role { font-size: 15px; margin-top: 6px; }
  .rule {
    width: 220px;
    height: 1px;
    background: var(--leaf);
    margin: 14px 0 12px;
  }
  .contact-list { list-style: none; }
  .contact-list li {
    display: flex;
    align-items: center;
    gap: 10px;
    font-size: 15px;
    line-height: 1.45;
  }
  .contact-list svg { width: 12px; height: 12px; flex: none; }
  .address { font-size: 15px; line-height: 1.35; }

  /* Back side */
  .card-back { background: var(--forest); }
  .pattern-field {
    position: absolute;
    inset: 0;
    background: linear-gradient(135deg, var(--forest-deep) 0%, var(--forest) 55%, var(--forest-soft) 100%);
  }
  .back-mark {
    position: absolute;
    right: 48px;
    bottom: 62px;
    color: var(--paper);
    font-weight: 700;
    font-size: 30px;
    letter-spacing: 2px;
  }
</style>
</head>
<body>

  <section class="card card-front" aria-label="Card front">
    <div class="brand-panel">
      <span class="brand-name">ZUB Capital</span>
    </div>
    <div class="details">
      <svg class="sweep" viewBox="0 0 370 300" preserveAspectRatio="none" aria-hidden="true">
        <path d="M170 300 C 210 170, 280 60, 370 20" fill="none" stroke="rgba(255,255,255,0.12)" stroke-width="14"/>
      </svg>
      <h1 class="person-name">MARTEN OAKLEY</h1>
      <p class="person-role">Director/Founder</p>
      <div class="rule"></div>
      <ul class="contact-list">
        <li>
          <svg viewBox="0 0 12 12" aria-hidden="true"><path d="M2.5 1 L4.5 1 L5.2 3.5 L4 4.5 C4.6 6 6 7.4 7.5 8 L8.5 6.8 L11 7.5 L11 9.5 C11 10.3 10.3 11 9.5 11 C5 11 1 7 1 2.5 C1 1.7 1.7 1 2.5 1Z" fill="var(--leaf)"/></svg>
          123-480-2917
        </li>
        <li>
          <svg viewBox="0 0 12 12" aria-hidden="true"><rect x="0.5" y="2" width="11" height="8" fill="var(--leaf)"/><path d="M0.5 2 L6 6.5 L11.5 2" fill="none" stroke="var(--forest)" stroke-width="1"/></svg>
          info@zub.capital
        </li>
        <li>
          <svg viewBox="0 0 12 12" aria-hidden="true"><circle cx="6" cy="6" r="5.5" fill="var(--leaf)"/><path d="M0.5 6 H11.5 M6 0.5 C3.5 3 3.5 9 6 11.5 M6 0.5 C8.5 3 8.5 9 6 11.5" fill="none" stroke="var(--forest)" stroke-width="0.8"/></svg>
          www.zub.capital
        </li>
      </ul>
      <div class="rule"></div>
      <p class="address">88 Harbour Row<br>Northland CD 3017</p>
    </div>
  </section>

  <section class="card card-back" aria-label="Card back">
    <div class="pattern-field" role="img" aria-label="Repeating embossed brand monogram pattern in dark and mid green tones"></div>
    <span class="back-mark">ZUB</span>
  </section>

</body>
</html>
```